BRISKLY sparkling water needs new artwork! Based in Southern California

"Briskly" is a new sparkling water company based in Southern California that offers refreshing flavors (lime, cherry, & mango) with B vitamins and antioxidants.

We would like to see packaging designs for standard 12oz cans for each of the three flavors.
Our initial preference is to have individual artwork for each flavor.

Attached are examples of competitors' designs.
Updates

We are extending the deadline for the Thanksgiving Holiday. Thank you all for your contributions.

```html
<!DOCTYPE html>
<html lang="en">
<head>
<meta charset="utf-8">
<title>Briskly Sparkling Water – 109 mm LF Label Template</title>
<link href="https://fonts.googleapis.com/css2?family=Open+Sans:wght@400;800&family=Source+Sans+3:wght@400;700&family=Roboto+Condensed:wght@400&family=Oswald:wght@500;700&display=swap" rel="stylesheet">
<style>
  :root {
    --guide: #a58ac4;
    --label-yellow: #f3e639;
    --panel-green: #7db652;
    --ink: #1a1a1a;
    --white: #ffffff;
    --fruit-red: #d9202e;
    --art-yellow: #f1e64a;
    --art-green: #b9d35a;
  }
  html, body {
    margin: 0;
    padding: 0;
    width: 1200px;
    height: 714px;
    overflow: hidden;
    background: var(--white);
  }
  .canvas {
    position: relative;
    width: 1200px;
    height: 714px;
    overflow: hidden;
    font-family: "Open Sans", sans-serif;
  }
  .guides { position: absolute; inset: 0; }
  .guide-text {
    position: absolute;
    color: var(--guide);
    font-family: "Source Sans 3", sans-serif;
    font-size: 12px;
    line-height: 1;
    white-space: nowrap;
  }
  .template-title { left: 0; width: 1218px; top: -6px; text-align: center; font-size: 27px; }
  .lf-width { left: 572px; top: 69px; font-size: 13px; }
  .clear-1mm { left: 123px; top: 49px; }
  .clear-5mm { left: 1001px; top: 49px; }
  .transition-title { left: 1068px; top: 49px; font-weight: 700; font-size: 14px; }
  .transition-note {
    left: 1068px; top: 65px;
    font-family: "Roboto Condensed", sans-serif;
    font-size: 10px;
  }
  .clear-top-left { left: -4px; top: 132px; }
  .clear-bottom-left { left: 0; top: 616px; }
  .clear-top-right { left: 1116px; top: 132px; }
  .clear-bottom-right { left: 1121px; top: 616px; }
  .cut-height { left: 1063px; top: 350px; font-size: 13px; line-height: 17px; }
  .slit-width {
    left: 520px; top: 647px; width: 130px;
    text-align: center;
    font-family: "Roboto Condensed", sans-serif;
    font-size: 13px; line-height: 16px;
  }
  .bleed-note { left: 129px; top: 692px; width: 100px; text-align: center; font-size: 9px; line-height: 12px; }
  .bkgd-note { left: 911px; top: 675px; width: 100px; text-align: center; font-size: 9px; line-height: 12px; }

  .brand-name {
    position: absolute;
    margin: 0;
    color: var(--ink);
    font-family: "Open Sans", sans-serif;
    font-weight: 800;
    letter-spacing: -1px;
    line-height: 1;
    text-align: center;
  }
  .brand-name--side { left: 196px; top: 210px; width: 132px; font-size: 38px; }
  .brand-name--front { left: 496px; top: 208px; width: 206px; font-size: 56px; }

  .copy-panel {
    position: absolute;
    left: 170px; top: 264px;
    width: 193px; height: 334px;
    box-sizing: border-box;
    background: var(--panel-green);
    border: 1.5px solid var(--ink);
    color: var(--white);
    text-align: center;
    font-size: 12.4px;
    line-height: 17px;
  }
  .copy-panel p { margin: 0; }
  .copy-panel .copy-lead { position: absolute; left: 1px; right: 1px; top: 7px; }
  .copy-panel .copy-rule {
    position: absolute; left: 24px; width: 133px; top: 121px;
    height: 3px; background: var(--white);
  }
  .copy-panel .copy-body { position: absolute; left: 1px; right: 1px; top: 140px; }

  .front-art {
    position: absolute;
    left: 394px; top: 266px;
    width: 400px; height: 330px;
    border-radius: 40% 40% 30% 30%;
    background:
      radial-gradient(ellipse 22% 26% at 28% 82%, #8fbf55 0 70%, transparent 100%),
      radial-gradient(ellipse at 50% 45%, var(--art-yellow) 0 40%, var(--art-green) 100%);
  }

  .product-badge {
    position: absolute;
    left: 486px; top: 310px;
    width: 221px; height: 140px;
    box-sizing: border-box;
    background: var(--white);
    border: 3px solid var(--ink);
    border-radius: 46% 46% 30% 30% / 30% 30% 40% 40%;
  }
  .product-name {
    position: absolute;
    margin: 0;
    left: 486px; width: 221px;
    text-align: center;
    color: var(--ink);
    font-family: "Oswald", sans-serif;
    font-weight: 700;
    text-transform: uppercase;
    line-height: 1;
    white-space: nowrap;
  }
  .product-name--top { top: 330px; font-size: 46px; letter-spacing: -1px; }
  .product-name--bottom { top: 380px; font-size: 60px; letter-spacing: -1px; }

  .benefit-band {
    position: absolute;
    left: 510px; top: 452px;
    width: 168px; height: 32px;
    box-sizing: border-box;
    background: var(--panel-green);
    border: 1.5px solid var(--ink);
    text-align: center;
    font-family: "Oswald", sans-serif;
    text-transform: uppercase;
    line-height: 1;
  }
  .benefit-band .benefit-main {
    display: block;
    margin-top: 2px;
    color: var(--fruit-red);
    font-weight: 700;
    font-size: 16px;
    letter-spacing: 0.3px;
  }
  .benefit-band .benefit-sub {
    display: block;
    margin-top: 0;
    color: var(--white);
    font-weight: 500;
    font-size: 9px;
    letter-spacing: 0.3px;
  }

  .flavor-bubble {
    position: absolute;
    left: 584px; top: 495px;
    width: 130px; height: 92px;
    box-sizing: border-box;
    background: var(--panel-green);
    border: 2px solid var(--ink);
    border-radius: 50% 55% 45% 30% / 55% 50% 50% 45%;
    color: var(--white);
    font-family: "Oswald", sans-serif;
    font-weight: 700;
    text-transform: uppercase;
    text-align: center;
    line-height: 1;
  }
  .flavor-bubble .flavor-name { display: block; margin-top: 10px; font-size: 34px; }
  .flavor-bubble .flavor-word { display: block; margin-top: 0; font-size: 28px; }

  .net-content {
    position: absolute;
    left: 600px; top: 592px; width: 104px;
    text-align: center;
    color: var(--white);
    font-family: "Oswald", sans-serif;
    font-weight: 500;
    font-size: 12px;
    letter-spacing: 0.5px;
    text-transform: uppercase;
  }

  .info-box {
    position: absolute;
    left: 821px; width: 171px;
    background: var(--white);
    color: var(--ink);
    font-size: 12.5px;
    display: flex;
    align-items: center;
    justify-content: center;
  }
  .nutrition-box { top: 228px; height: 256px; padding-top: 24px; box-sizing: border-box; }
  .barcode-area { top: 517px; height: 65px; padding-top: 12px; box-sizing: border-box; }
</style>
</head>
<body>
<main class="canvas">

  <svg class="guides" width="1200" height="714" viewBox="0 0 1200 714" aria-hidden="true">
    <rect x="145" y="133" width="875" height="494" fill="var(--label-yellow)"/>
    <g fill="none" stroke="var(--guide)" stroke-width="1">
      <rect x="145.5" y="133.5" width="897" height="493"/>
      <rect x="149.5" y="141.5" width="873" height="477"/>
      <rect x="376.5" y="92.5" width="435" height="546"/>
      <line x1="119" y1="190" x2="1069" y2="190" stroke-dasharray="8 6"/>
      <line x1="153" y1="92" x2="153" y2="671" stroke-dasharray="1 2" stroke-width="0.6"/>
      <line x1="1019" y1="116" x2="1019" y2="655" stroke-dasharray="1 2" stroke-width="0.6"/>
      <line x1="145" y1="71" x2="145" y2="120" stroke-width="0.6"/>
      <line x1="149" y1="71" x2="149" y2="120" stroke-width="0.6"/>
      <line x1="1023" y1="71" x2="1023" y2="120" stroke-width="0.6"/>
      <line x1="1043" y1="71" x2="1043" y2="120" stroke-width="0.6"/>
      <line x1="67" y1="133" x2="117" y2="133" stroke-width="0.6"/>
      <line x1="67" y1="141" x2="117" y2="141" stroke-width="0.6"/>
      <line x1="69" y1="619" x2="119" y2="619" stroke-width="0.6"/>
      <line x1="69" y1="627" x2="119" y2="627" stroke-width="0.6"/>
      <line x1="1059" y1="133" x2="1109" y2="133" stroke-width="0.6"/>
      <line x1="1059" y1="141" x2="1109" y2="141" stroke-width="0.6"/>
      <line x1="1064" y1="619" x2="1114" y2="619" stroke-width="0.6"/>
      <line x1="1064" y1="627" x2="1114" y2="627" stroke-width="0.6"/>
      <line x1="149" y1="640" x2="149" y2="676" stroke-width="0.8"/>
      <line x1="1042" y1="640" x2="1042" y2="680" stroke-width="0.8"/>
      <line x1="152" y1="657" x2="517" y2="657" stroke-width="0.8"/>
      <line x1="656" y1="657" x2="1039" y2="657" stroke-width="0.8"/>
      <line x1="1079" y1="83" x2="1037" y2="135" stroke-width="1.2"/>
    </g>
    <g fill="var(--guide)">
      <circle cx="1079" cy="83" r="3"/>
      <polygon points="1034,139 1036,129 1042,134"/>
      <polygon points="150,657 156,654 156,660"/>
      <polygon points="1042,657 1036,654 1036,660"/>
    </g>
  </svg>

  <span class="guide-text template-title">109 mm LF_4.875”_Template</span>
  <span class="guide-text lf-width">109 mm LF</span>
  <span class="guide-text clear-1mm">1 mm clear</span>
  <span class="guide-text clear-5mm">5 mm clear</span>
  <span class="guide-text transition-title">Transitional Area</span>
  <span class="guide-text transition-note">(transitions from sidewall to neck)</span>
  <span class="guide-text clear-top-left">2 mm clear</span>
  <span class="guide-text clear-bottom-left">2 mm clear</span>
  <span class="guide-text clear-top-right">2 mm clear</span>
  <span class="guide-text clear-bottom-right">2 mm clear</span>
  <span class="guide-text cut-height">4.875” Cut Height<br>123.825 MM</span>
  <span class="guide-text slit-width">225 MM SLIT WIDTH<br>8.8583”</span>
  <span class="guide-text bleed-note">1mm Bkgd Bleed<br>Overlap</span>
  <span class="guide-text bkgd-note">2mm Bkgd Only<br>No Text/Art</span>

  <h2 class="brand-name brand-name--side">Briskly</h2>
  <section class="copy-panel">
    <p class="copy-lead">Lorem Ipsum is simply dummy text of the printing and typesetting industry. Lorem Ipsum has been the industry's standard dummy text ever since the 1500s, when an</p>
    <div class="copy-rule"></div>
    <p class="copy-body">unknown printer took a galley of type and scrambled it to make a type specimen book. It has survived not only five centuries, but also the leap into electronic typesetting, remai-ning essentially unchanged. It was popularised in the 1960s with the release of Letrafix sheets containing Lorem Ipsum passages, and</p>
  </section>

  <div class="front-art" role="img" aria-label="Illustration: lemons with leaves, breaking waves, bubbles and a lime around the product name"></div>
  <h1 class="brand-name brand-name--front">Briskly</h1>

  <div class="product-badge"></div>
  <p class="product-name product-name--top">Sparkling</p>
  <p class="product-name product-name--bottom">Water</p>

  <div class="benefit-band">
    <span class="benefit-main">With real fruit</span>
    <span class="benefit-sub">and B vitamins</span>
  </div>

  <div class="flavor-bubble">
    <span class="flavor-name">Lime</span>
    <span class="flavor-word">Flavor</span>
  </div>

  <span class="net-content">12oz (355ml)</span>

  <div class="info-box nutrition-box">Nutrition box</div>
  <div class="info-box barcode-area">Barcode</div>

</main>
</body>
</html>
```